letterhead design

We have a business card with logo, ink etc and want to develop letterhead that uses the elements of the business card logo.
Must haves...and they should be designed in, not just plopped in :)
Dr. Marlo Quint
2718 W Juniper Street
Fresno, CA 93604
559-381-7642 p
559-381-7655 f
info@brightwellchiropractic.example
www.brightwellchiropractic.example
www.facebook.example/brightwellchiro

Rather than just have the logo on the page, is there someway to silkscreen it in the background to fill the page?

Reason: I was out of town for a week.

Business

• I'd like the logo somehow silk screened in the background of the paper as well.

```html
<!DOCTYPE html>
<html lang="en">
<head>
<meta charset="utf-8">
<title>Brightwell Chiropractic – Letterhead</title>
<link rel="stylesheet" href="https://fonts.googleapis.com/css2?family=Cabin:wght@500;700&display=swap">
<style>
  :root {
    --ink: #0d2b52;
    --silk: #eef1f6;
    --trim: #5fe3ef;
    --paper: #ffffff;
  }
  html, body {
    margin: 0;
    padding: 0;
    width: 1200px;
    height: 848px;
    overflow: hidden;
    background: var(--paper);
    font-family: "Cabin", "Gill Sans", sans-serif;
  }
  .sheet {
    position: absolute;
    left: 254px;
    top: 228px;
    width: 685px;
    height: 297px;
    border: 1px dashed var(--trim);
    box-sizing: border-box;
    overflow: hidden;
    background: var(--paper);
  }
  .silkscreen {
    position: absolute;
    left: 120px;
    top: 150px;
    transform: rotate(-22deg);
    transform-origin: left top;
    color: var(--silk);
    font-weight: 700;
    line-height: 0.95;
    white-space: nowrap;
    pointer-events: none;
    user-select: none;
  }
  .silkscreen .silk-name {
    display: block;
    font-size: 118px;
    letter-spacing: 4px;
  }
  .silkscreen .silk-sub {
    display: block;
    font-size: 56px;
    letter-spacing: 10px;
    margin-left: 150px;
  }
  .brand {
    position: absolute;
    left: 26px;
    top: 22px;
    width: 147px;
    height: 66px;
    display: flex;
    align-items: center;
    gap: 8px;
    color: var(--ink);
    font-weight: 700;
  }
  .brand-mark {
    flex: 0 0 auto;
    width: 16px;
    height: 16px;
    background: var(--ink);
  }
  .brand-name {
    font-size: 16px;
    line-height: 1.05;
  }
  .contact {
    position: absolute;
    left: 183px;
    top: 36px;
    color: var(--ink);
    font-weight: 500;
    font-size: 8px;
    line-height: 11px;
    white-space: nowrap;
  }
  .contact .doctor {
    font-weight: 700;
    font-size: 9.5px;
    margin-bottom: 1px;
  }
</style>
</head>
<body>
  <main class="sheet">
    <div class="silkscreen" aria-hidden="true">
      <span class="silk-name">BRIGHTWELL</span>
      <span class="silk-sub">CHIROPRACTIC</span>
    </div>

    <div class="brand">
      <span class="brand-mark"></span>
      <span class="brand-name">Brightwell<br>Chiropractic</span>
    </div>

    <address class="contact" style="font-style:normal">
      <div class="doctor">Dr. Marlo Quint</div>
      <div>2718 W Juniper Street, Fresno, CA 93604</div>
      <div>Phone: 559-381-7642&nbsp;&nbsp;Fax: 559-381-7655</div>
    </address>
  </main>
</body>
</html>
```